Business Card Design Project

Company Name - Solvane Care

Wellness consulting and training company. Run through a medical centre.

Main colour themes are orange and blue, as in the logo. Want to replicate same effect with business cards.

To give a sense of freedom and potential as per the company name.

Want the business card to be in line with stationary design, which I have launched as well.

Double sided with design and colour on one side and details on other side.

Reason: Need business card and stationary design to be teed up.

Target Market(s)

35 to 65 age group.
New age and trendy

Industry/Entity Type

Training

Requirements
Must have
• Colours orange and blue as per logo
Nice to have
• Design to be similar to stationary design, letterhead and envelopes

```html
<!DOCTYPE html>
<html lang="en">
<head>
<meta charset="utf-8">
<title>Solvane Care – Business Cards</title>
<link rel="stylesheet" href="https://fonts.googleapis.com/css2?family=Lato:wght@400;700;900&display=swap">
<style>
  :root {
    --stage: #e9e6e2;
    --card: #ffffff;
    --blue: #1f4e9c;
    --blue-light: #5a95cf;
    --orange: #f26f21;
    --ink: #1b1b1b;
    --shadow: rgba(60, 40, 20, 0.22);
  }
  * { margin: 0; padding: 0; box-sizing: border-box; }
  html, body { width: 1200px; height: 900px; overflow: hidden; }
  body {
    background: var(--stage);
    font-family: "Lato", Arial, sans-serif;
    color: var(--ink);
    position: relative;
  }
  .card {
    position: absolute;
    width: 640px;
    height: 366px;
    background: var(--card);
    border-radius: 16px;
    box-shadow: 0 10px 28px var(--shadow);
    left: 280px;
  }
  .card--front { top: 48px; }
  .card--back { top: 478px; }

  .wordmark {
    display: flex;
    align-items: center;
    gap: 14px;
    color: var(--blue);
    font-weight: 400;
    white-space: nowrap;
  }
  .wordmark__dot {
    border-radius: 50%;
    background: var(--blue-light);
    flex: none;
  }
  .card--front .wordmark {
    position: absolute;
    left: 50%; top: 50%;
    transform: translate(-50%, -50%);
    font-size: 64px;
    letter-spacing: -0.5px;
  }
  .card--front .wordmark__dot { width: 40px; height: 40px; }

  .card--back .wordmark {
    position: absolute;
    left: 250px; top: 92px;
    font-size: 34px;
    gap: 10px;
  }
  .card--back .wordmark__dot { width: 22px; height: 22px; }

  .holder {
    position: absolute;
    left: 56px; top: 200px;
    text-align: right;
    width: 250px;
  }
  .holder__name {
    color: var(--blue);
    font-weight: 900;
    font-size: 22px;
    letter-spacing: 0.5px;
  }
  .holder__role {
    color: var(--orange);
    font-weight: 700;
    font-size: 15px;
    margin-top: 2px;
  }
  .holder__address {
    margin-top: 30px;
    font-weight: 700;
    font-size: 14px;
    line-height: 1.45;
  }

  .divider {
    position: absolute;
    left: 330px; top: 168px;
    width: 3px; height: 150px;
    background: linear-gradient(to bottom, rgba(31,78,156,0), var(--blue) 50%, rgba(31,78,156,0));
  }

  .contacts {
    position: absolute;
    left: 352px; top: 178px;
    list-style: none;
    font-size: 14px;
    line-height: 1;
  }
  .contacts li {
    display: flex;
    align-items: center;
    gap: 9px;
    height: 22px;
  }
  .contacts svg { width: 14px; height: 14px; flex: none; }
  .contacts .web { font-weight: 700; padding-left: 23px; }
  .contacts .web span { color: var(--blue); }
</style>
</head>
<body>
  <section class="card card--front" aria-label="Card front">
    <div class="wordmark">
      <span class="wordmark__name">Solvane Care</span>
      <span class="wordmark__dot"></span>
    </div>
  </section>

  <section class="card card--back" aria-label="Card back">
    <div class="wordmark">
      <span class="wordmark__name">Solvane Care</span>
      <span class="wordmark__dot"></span>
    </div>

    <div class="holder">
      <p class="holder__name">YOUR NAME</p>
      <p class="holder__role">Centre Director</p>
      <p class="holder__address">Via Collerosa,<br>18 62010 Montelago (MC), Italy</p>
    </div>

    <div class="divider"></div>

    <ul class="contacts">
      <li>
        <svg viewBox="0 0 14 14" aria-hidden="true"><path fill="#1f4e9c" d="M1 5c0-2 2-3 6-3s6 1 6 3v1h-3V5H4v1H1zM3 7h8l1 5H2z"/></svg>
        (+44) 555 0148
      </li>
      <li>
        <svg viewBox="0 0 14 14" aria-hidden="true"><rect x="2" y="2" width="10" height="10" fill="none" stroke="#1f4e9c" stroke-width="1.5"/></svg>
        +39 300 5550172
      </li>
      <li>
        <svg viewBox="0 0 14 14" aria-hidden="true"><rect x="1" y="3" width="12" height="8" fill="#1f4e9c"/><path d="M1 3l6 5 6-5" fill="none" stroke="#fff" stroke-width="1.2"/></svg>
        info@solvanecare.com
      </li>
      <li class="web">www.<span>solvanecare</span>.com</li>
    </ul>
  </section>
</body>
</html>
```